​Silver Harbor Rhythm provides personal, friendly service in a fun and high energy environment. We are based in Vermont.

We would like a card that appeals to a wide range of audiences as we do a wide range of events. Please feel free to check out our website silverharborrhythm.net for inspiration.

Target Market(s)

weddings, corporate, birthday parties, colleges

Industry/Entity Type

Business

Contact Information for Business Card

Silver Harbor Rhythm
Providing Entertainment For All Occasions
555 274 9160
silverharborrhythm@mailnest.net
silverharborrhythm.net

```html
<!DOCTYPE html>
<html lang="en">
<head>
<meta charset="UTF-8">
<title>Silver Harbor Rhythm – Business Card</title>
<link rel="stylesheet" href="https://fonts.googleapis.com/css2?family=Open+Sans:wght@400;600;700&display=swap">
<style>
  :root {
    --forest: #2f5d1c;
    --wine: #7a1f24;
    --ink: #333333;
    --paper: #ffffff;
    --backdrop: #e9e7e3;
  }
  * { margin: 0; padding: 0; box-sizing: border-box; }
  html, body {
    width: 1200px; height: 1200px; overflow: hidden;
    background: var(--backdrop);
    font-family: "Open Sans", Arial, sans-serif;
  }
  .canvas { position: relative; width: 1200px; height: 1200px; }
  .card {
    position: absolute; left: 150px; width: 900px; height: 520px;
    background: var(--paper); border-radius: 36px; overflow: hidden;
    box-shadow: 0 6px 18px rgba(0,0,0,0.18);
  }
  .card--front { top: 50px; }
  .card--back { top: 630px; }

  .front-band { position: absolute; inset: 0; width: 900px; height: 520px; }

  .brand-name {
    position: absolute; left: 0; right: 0; text-align: center;
    color: var(--forest); font-weight: 700; letter-spacing: 2px;
    text-transform: uppercase; white-space: nowrap;
  }
  .card--front .brand-name { top: 110px; font-size: 44px; }
  .card--back .brand-name { top: 190px; font-size: 60px; letter-spacing: 3px; }

  .tagline {
    position: absolute; left: 0; right: 0; text-align: center;
    color: var(--wine); font-weight: 400; text-transform: uppercase;
    white-space: nowrap;
  }
  .card--front .tagline { top: 172px; font-size: 15px; letter-spacing: 4px; }
  .card--back .tagline { top: 280px; font-size: 20px; letter-spacing: 6px; }

  .holder {
    position: absolute; top: 232px; left: 0; right: 0; text-align: center;
    color: var(--forest); font-size: 28px; font-weight: 400;
  }
  .holder strong { font-weight: 700; }

  .contact {
    position: absolute; left: 0; right: 0; color: var(--paper);
    font-size: 22px; display: flex; justify-content: center; align-items: center; gap: 10px;
  }
  .contact--address { top: 352px; }
  .contact--phone { top: 398px; }
  .contact--online { top: 448px; gap: 34px; }
  .contact-item { display: flex; align-items: center; gap: 10px; }
  .contact-icon { width: 22px; height: 22px; flex: none; }

  .web-address {
    position: absolute; left: 0; right: 0; top: 420px; text-align: center;
    color: var(--ink); font-size: 30px; letter-spacing: 1.5px;
  }
</style>
</head>
<body>
<main class="canvas">

  <section class="card card--front">
    <svg class="front-band" viewBox="0 0 900 520" aria-hidden="true">
      <path d="M0 350 Q 450 318 900 282 L900 520 L0 520 Z" fill="var(--forest)"/>
      <path d="M0 333 Q 450 301 900 265" fill="none" stroke="var(--wine)" stroke-width="5"/>
    </svg>
    <div class="brand-name">Silver Harbor Rhythm</div>
    <p class="tagline">Providing Entertainment For All Occasions</p>
    <p class="holder"><strong>Your Name,</strong> Title</p>
    <p class="contact contact--address">Sreet Name, City Name, Zip Code-00000</p>
    <p class="contact contact--phone">
      <svg class="contact-icon" viewBox="0 0 24 24" aria-hidden="true">
        <circle cx="12" cy="12" r="11" fill="var(--paper)"/>
        <path d="M8 6 L10 6 L11 9 L9.5 10.5 Q11 13.5 13.5 14.5 L15 13 L18 14 L18 16 Q17 18 15 18 Q8 16 6 9 Q6 7 8 6 Z" fill="var(--forest)"/>
      </svg>
      555 274 9160
    </p>
    <div class="contact contact--online">
      <span class="contact-item">
        <svg class="contact-icon" viewBox="0 0 24 24" aria-hidden="true">
          <circle cx="12" cy="12" r="11" fill="var(--paper)"/>
          <rect x="6" y="8" width="12" height="8" fill="var(--forest)"/>
          <path d="M6 8 L12 13 L18 8" fill="none" stroke="var(--paper)" stroke-width="1.2"/>
        </svg>
        silverharborrhythm@mailnest.net
      </span>
      <span class="contact-item">
        <svg class="contact-icon" viewBox="0 0 24 24" aria-hidden="true">
          <circle cx="12" cy="12" r="11" fill="var(--paper)"/>
          <circle cx="12" cy="12" r="6.5" fill="none" stroke="var(--forest)" stroke-width="1.4"/>
          <ellipse cx="12" cy="12" rx="3" ry="6.5" fill="none" stroke="var(--forest)" stroke-width="1.2"/>
          <line x1="5.5" y1="12" x2="18.5" y2="12" stroke="var(--forest)" stroke-width="1.2"/>
        </svg>
        www.silverharborrhythm.net
      </span>
    </div>
  </section>

  <section class="card card--back">
    <div class="brand-name">Silver Harbor Rhythm</div>
    <p class="tagline">Providing Entertainment For All Occasions</p>
    <p class="web-address">www.silverharborrhythm.net</p>
  </section>

</main>
</body>
</html>
```